WP website design (Harrowgate)

We need a wordpress design for an established auction and real estate company based in Florida. The winning design will incorporate a professional color scheme with company logo in a clean layout. The design needs to consider that this will be developed on a responsive theme. Colors are those that will highlight the logo.

Industry/Entity Type

Real Estate

Font styles to use
Serif
Sans Serif

Colors

Designer to choose colors to be used in the design.

Requirements
Must have
• Navigation:
1) Home
2) Auctions
3) Online Auctions
4) About Us
5) Services
6) Real Estate Listings
7) References
8) Contact Us

Colors will be blue (#000066) / red (#B10000) and black or other complementary color. Tagline to be used "Since 1977, Proven Results." Slideshow to be placed in the header or body of home page - please use stock real estate image.

Widgets: 1) Email Sign-up 2) Social media icons for FB and LinkedIn 3) Featured Listings 4) Testimonials 5) Register button

Footer will have smaller company logo, attached logos and contact info:
Phone: (555) 261-0948 Mobile: (555) 718-3062
Email: mirelharrowgate@quellmail.example
Address: 58 E. Tamsin Avenue, Ste 410, Pensacola, FL 32599
Nice to have
• Use of a drop down menu:
Auctions-
1) Upcoming Auctions
2) Past Auctions

```html
<!DOCTYPE html>
<html lang="en">
<head>
<meta charset="utf-8">
<title>Harrowgate Auctions</title>
<link href="https://fonts.googleapis.com/css2?family=Mulish:wght@400;600;700&family=Merriweather:wght@400&display=swap" rel="stylesheet">
<style>
:root{
  --navy:#2e3192;
  --link:#1a22b5;
  --red:#d7232e;
  --yellow:#fff200;
  --ink:#333;
  --muted:#8a8a8a;
  --panel:#f2f2f2;
  --dark:#3a3a3a;
  --white:#fff;
}
*{box-sizing:border-box;margin:0;padding:0}
html,body{width:1200px;height:2184px;overflow:hidden}
body{position:relative;background:var(--white);font-family:"Mulish",Arial,sans-serif;color:var(--ink)}
.abs{position:absolute}

/* header */
.brand{left:131px;top:30px;display:flex;align-items:center;gap:10px}
.brand-mark{width:30px;height:30px;background:var(--red)}
.brand-name{font-size:28px;font-weight:700;color:var(--navy);letter-spacing:.5px}
.search{left:866px;top:33px;width:201px;height:36px;border:1px solid #ddd;display:flex;align-items:center}
.search span{flex:1;padding-left:14px;font-size:12px;font-style:italic;color:#aaa}
.search i{width:40px;height:100%;border-left:1px solid #ddd;display:flex;align-items:center;justify-content:center}

.nav{left:0;top:102px;width:1200px;height:45px;background:var(--navy)}
.nav a{position:absolute;top:0;height:45px;line-height:45px;font-size:12px;font-weight:600;color:var(--white);text-decoration:none;transform:translateX(-50%);white-space:nowrap}
.nav a.active{background:var(--yellow);color:var(--navy);width:86px;text-align:center}
.dropdown{left:215px;top:147px;width:184px;height:82px;background:var(--yellow);padding:10px 0 0 18px;z-index:3}
.dropdown li{list-style:none;font-size:12px;color:var(--navy);line-height:34px;white-space:nowrap}
.dropdown li::before{content:"→";margin-right:10px;font-size:10px}

/* hero */
.hero{left:0;top:147px;width:1200px;height:446px;background:linear-gradient(90deg,#cfa98c 0%,#d9c07a 25%,#e6e4e6 48%,#ececef 100%)}
.hero-title{right:133px;top:256px;font-size:35px;color:var(--red);font-weight:400;text-align:right}
.hero-text{right:133px;top:324px;width:440px;font-size:13px;line-height:24.5px;color:#555;text-align:right}
.btn-register{left:908px;top:424px;width:159px;height:42px;background:var(--red);color:var(--white);font-size:15px;display:flex;align-items:center;justify-content:center}
.dots{left:540px;top:563px;width:130px;height:30px;background:rgba(60,60,60,.65);border-radius:14px 14px 0 0;display:flex;gap:7px;justify-content:center;align-items:center}
.dots b{width:12px;height:12px;border-radius:50%;background:#aaa}
.dots b:first-child{background:var(--yellow)}

/* welcome */
.welcome{left:0;top:656px;width:1200px;text-align:center;font-size:26px;font-weight:400;color:#333}
.welcome em{font-style:normal;color:var(--link)}
.welcome-text{left:146px;top:710px;width:910px;text-align:center;font-size:12.5px;line-height:24px;color:var(--muted)}

/* auctions */
.panel{background:var(--panel)}
.panel-title{left:147px;top:860px;font-size:24px;font-weight:400;color:#333}
.circle-arrow{width:24px;height:24px;border:2px solid #ccc;border-radius:50%}
.card{left:147px;width:655px;height:426px}
.card .photo{position:absolute;left:0;top:0;width:322px;height:190px;border:3px solid var(--white);background:linear-gradient(180deg,#7ea7d6 0%,#a9c3de 45%,#9a7a5e 60%,#6f8d4f 100%)}
.card h3{position:absolute;left:345px;top:0;font-size:19px;font-weight:600;color:var(--link)}
.card .desc{position:absolute;left:346px;top:34px;width:310px;font-size:12.5px;line-height:22px;color:var(--muted)}
.card .rule{position:absolute;left:345px;width:310px;height:1px;background:#ddd}
.card h4{position:absolute;left:348px;font-size:18px;font-weight:400;color:#333}
.card .date{position:absolute;left:351px;font-size:12px;color:#666}
.card .date b{color:var(--red);font-weight:400}
.btn-ghost{position:absolute;width:147px;height:39px;background:var(--white);border:1px solid #ddd;display:flex;align-items:center;padding-left:18px;gap:14px;font-size:13px;color:#444}
.btn-addr{position:absolute;left:6px;top:355px;width:313px;height:44px;background:linear-gradient(#555,#3d3d3d);color:var(--white);font-size:14px;display:flex;align-items:center;justify-content:center;gap:14px}
.btn-bid{position:absolute;left:344px;top:355px;width:311px;height:44px;background:var(--navy);color:var(--white);font-size:14.5px;display:flex;align-items:center;justify-content:center}

/* sidebar */
.signup{left:850px;top:839px;width:220px;height:173px;background:var(--navy);color:var(--white);padding:20px 19px}
.side-title{font-size:16px;font-weight:600}
.signup p{font-size:12px;margin-top:8px}
.signup .field{position:absolute;left:19px;top:80px;width:179px;height:32px;background:var(--white);font-size:11px;font-style:italic;color:#999;padding:9px 14px}
.signup .submit{position:absolute;left:124px;top:126px;width:74px;height:29px;background:var(--yellow);color:var(--navy);font-size:12px;display:flex;align-items:center;justify-content:center}
.featured{left:850px;top:1040px;width:220px;height:369px;background:linear-gradient(#5e5e5e,#474747);color:var(--white);padding:20px 19px}
.featured ul{margin-top:10px}
.featured li{list-style:none;font-size:12.5px;line-height:32.6px}
.featured li::before{content:"→";margin-right:12px;font-size:11px}
.featured .more{position:absolute;left:128px;top:323px;width:73px;height:28px;background:var(--yellow);color:var(--navy);font-size:12px;display:flex;align-items:center;justify-content:center}
.testimonial{left:850px;top:1440px;width:220px;height:205px;background:#e2e2e2;padding:20px 19px}
.testimonial .side-title{color:#333;font-weight:400;font-size:17px}
.testimonial blockquote{margin-top:22px;font-size:12.5px;line-height:22px;color:#666}
.testimonial blockquote::before{content:"“";font-size:28px;color:#bbb;line-height:0;margin-right:10px;vertical-align:-8px}
.testimonial .who{margin-top:16px;font-size:12.5px;color:var(--link)}
.testimonial .from{font-size:11.5px;font-style:italic;color:var(--muted)}

/* partners & footer */
.partners{left:0;top:1883px;width:1200px;height:126px;background:#fafafa}
.badge{position:absolute;top:34px;height:56px;background:#d9dbe6;border-radius:4px}
.footer{left:0;top:2009px;width:1200px;height:175px;background:var(--dark);color:#b5b5b5;font-size:12.5px}
.footer .item{position:absolute;top:36px;display:flex;gap:12px;line-height:20px;white-space:nowrap}
.footer .email{font-size:12px}
.footer .social{position:absolute;left:898px;top:44px;display:flex;gap:7px}
.footer .social b{width:29px;height:29px;border-radius:50%;background:#888;border:2px solid #ccc}
.footer .rule{position:absolute;left:0;top:108px;width:1200px;height:1px;background:#4a4a4a}
.footer .copy{position:absolute;left:0;top:136px;width:1200px;text-align:center;font-size:11px;color:#999}
</style>
</head>
<body>

<header>
  <div class="abs brand"><span class="brand-mark"></span><span class="brand-name">Harrowgate</span></div>
  <div class="abs search"><span>Search here...</span><i><svg width="17" height="17" viewBox="0 0 17 17"><circle cx="7" cy="7" r="5.5" fill="none" stroke="#555" stroke-width="2"/><line x1="11" y1="11" x2="16" y2="16" stroke="#555" stroke-width="2.4"/></svg></i></div>
  <nav class="abs nav">
    <a style="left:160px">HOME</a>
    <a class="active" style="left:258px">AUCTIONS</a>
    <a style="left:377px">ONLINE AUCTIONS</a>
    <a style="left:515px">ABOUT US</a>
    <a style="left:616px">SERVICES</a>
    <a style="left:750px">REAL ESTATE LISTINGS</a>
    <a style="left:894px">REFERENCES</a>
    <a style="left:1008px">CONTACT US</a>
  </nav>
  <ul class="abs dropdown"><li>Upcoming Auctions</li><li>Past Auctions</li></ul>
</header>

<section>
  <div class="abs hero" role="img" aria-label="Slideshow photo: hands holding a small model house"></div>
  <h1 class="abs hero-title">Since 1977, Proven Results</h1>
  <p class="abs hero-text">Lorem ipsum dolor sit amet, consectetur adipisicing elit, sed do eiusmod tempor incididunt ut labore et dolore magna aliqua. Ut enim ad minim veniam, quis nostrud exercitation ullamco laboris nisuq.</p>
  <div class="abs btn-register">Register Now &nbsp;»</div>
  <div class="abs dots"><b></b><b></b><b></b><b></b></div>
</section>

<section>
  <h2 class="abs welcome">Welcome to Our Website <em>Mainpage..</em></h2>
  <p class="abs welcome-text">Lorem ipsum dolor sit amet, consectetur adipisicing elit, sed do eiusmod tempor incididunt ut labore et dolore magna aliqua. Ut enim ad minim veniam, quis nostrud exercitation ullamco laboris nisi ut aliquip ex ea commodo consequat. Duis aute irure dolor in reprehenderit in voluptate velit esse cillum dolore eu fugiat nulla pariatur. Lorem ipsum dolor sit amet, consectetur adipisicing elit, sed do eiusmod tempor incididunt.</p>
</section>

<main>
  <div class="abs panel" style="left:131px;top:839px;width:699px;height:506px"></div>
  <h2 class="abs panel-title">Latest Auctions</h2>
  <div class="abs circle-arrow" style="left:787px;top:860px"></div>

  <div class="abs panel" style="left:131px;top:1370px;width:699px;height:454px"></div>

  <article class="abs card" style="top:919px">
    <div class="photo" role="img" aria-label="Brick house with a white garage door"></div>
    <h3>Finibus Bonorum et Malorum</h3>
    <p class="desc">Duis aute irure dolor in reprehenderit in voluptate vel esse cillum dolore eu fugiat nulla pariatur dolor sit amet, consectetur adipisicing elit</p>
    <div class="rule" style="top:116px"></div>
    <h4 style="top:129px">Online Bidding Only</h4>
    <p class="date" style="top:168px"><b>Begins:</b> Tuesday, May 30, 2017 at 11:00 AM EDT</p>
    <p class="date" style="top:194px"><b>Ends:</b> Wednesday, May 31, 2017 at 11:00 AM EDT</p>
    <div class="rule" style="top:227px"></div>
    <h4 style="top:240px">Live Off-Site Auction</h4>
    <p class="date" style="top:279px"><b>Begins:</b> Tuesday, May 30, 2017 at 11:00 AM EDT</p>
    <p class="date" style="top:305px"><b>Ends:</b> Wednesday, May 31, 2017 at 11:00 AM EDT</p>
    <div class="btn-ghost" style="left:6px;top:217px"><svg width="18" height="18" viewBox="0 0 18 18"><rect x="2" y="3" width="12" height="14" rx="1" fill="#555"/><circle cx="14" cy="14" r="4" fill="#555" stroke="#fff" stroke-width="1.5"/></svg>Details »</div>
    <div class="btn-ghost" style="left:173px;top:217px"><svg width="20" height="16" viewBox="0 0 20 16"><rect x="1" y="1" width="18" height="14" fill="none" stroke="#555" stroke-width="2"/><path d="M3 13l5-6 4 4 2-2 4 4z" fill="#555"/></svg>Photos »</div>
    <div class="btn-ghost" style="left:6px;top:278px"><svg width="20" height="14" viewBox="0 0 20 14"><rect x="0" y="1" width="13" height="12" rx="1" fill="#555"/><path d="M14 5l6-4v12l-6-4z" fill="#555"/></svg>Videos »</div>
    <div class="btn-addr"><svg width="13" height="18" viewBox="0 0 13 18"><path d="M6.5 0C3 0 0 2.8 0 6.4 0 11 6.5 18 6.5 18S13 11 13 6.4C13 2.8 10 0 6.5 0z" fill="#fff"/><circle cx="6.5" cy="6.4" r="2.4" fill="#4a4a4a"/></svg>P.O. Box 40716 Calder, VA 24099</div>
    <div class="btn-bid">Click here for Online Bidding &nbsp;»</div>
  </article>

  <article class="abs card" style="top:1401px">
    <div class="photo" role="img" aria-label="Two-storey suburban house with a double garage"></div>
    <h3>Finibus Bonorum et Malorum</h3>
    <p class="desc">Duis aute irure dolor in reprehenderit in voluptate vel esse cillum dolore eu fugiat nulla pariatur dolor sit amet, consectetur adipisicing elit</p>
    <div class="rule" style="top:116px"></div>
    <h4 style="top:129px">Online Bidding Only</h4>
    <p class="date" style="top:168px"><b>Begins:</b> Tuesday, May 30, 2017 at 11:00 AM EDT</p>
    <p class="date" style="top:194px"><b>Ends:</b> Wednesday, May 31, 2017 at 11:00 AM EDT</p>
    <div class="rule" style="top:227px"></div>
    <h4 style="top:240px">Live Off-Site Auction</h4>
    <p class="date" style="top:279px"><b>Begins:</b> Tuesday, May 30, 2017 at 11:00 AM EDT</p>
    <p class="date" style="top:305px"><b>Ends:</b> Wednesday, May 31, 2017 at 11:00 AM EDT</p>
    <div class="btn-ghost" style="left:6px;top:217px"><svg width="18" height="18" viewBox="0 0 18 18"><rect x="2" y="3" width="12" height="14" rx="1" fill="#555"/><circle cx="14" cy="14" r="4" fill="#555" stroke="#fff" stroke-width="1.5"/></svg>Details »</div>
    <div class="btn-ghost" style="left:173px;top:217px"><svg width="20" height="16" viewBox="0 0 20 16"><rect x="1" y="1" width="18" height="14" fill="none" stroke="#555" stroke-width="2"/><path d="M3 13l5-6 4 4 2-2 4 4z" fill="#555"/></svg>Photos »</div>
    <div class="btn-ghost" style="left:6px;top:278px"><svg width="20" height="14" viewBox="0 0 20 14"><rect x="0" y="1" width="13" height="12" rx="1" fill="#555"/><path d="M14 5l6-4v12l-6-4z" fill="#555"/></svg>Videos »</div>
    <div class="btn-addr"><svg width="13" height="18" viewBox="0 0 13 18"><path d="M6.5 0C3 0 0 2.8 0 6.4 0 11 6.5 18 6.5 18S13 11 13 6.4C13 2.8 10 0 6.5 0z" fill="#fff"/><circle cx="6.5" cy="6.4" r="2.4" fill="#4a4a4a"/></svg>P.O. Box 40716 Calder, VA 24099</div>
    <div class="btn-bid">Click here for Online Bidding &nbsp;»</div>
  </article>
</main>

<aside>
  <div class="abs signup">
    <div class="side-title">EMAIL SIGN-UP</div>
    <p>Lorem ipsum dolor sit amet elit</p>
    <div class="field">Enter Email...</div>
    <div class="submit">SUBMIT</div>
  </div>
  <div class="abs featured">
    <div class="side-title">FEATURED LISTINGS</div>
    <ul>
      <li>Duis aute irure dolor</li>
      <li>Reprehenderit in voluptate</li>
      <li>Velit esse cillum dolore eu</li>
      <li>Fugiat nulla pariatur</li>
      <li>Lorem ipsum dolor sit amet</li>
      <li>Consectetur adipisicing</li>
      <li>Sed do eiusmod</li>
      <li>Tempor incididunt</li>
    </ul>
    <div class="more">More ››</div>
  </div>
  <div class="abs testimonial">
    <div class="side-title">Testimonial</div>
    <div class="abs circle-arrow" style="left:182px;top:22px;width:21px;height:21px"></div>
    <blockquote>Duis aute irure dolor in reprehenderit in voluptate vel esse cillum dolore.</blockquote>
    <div class="who">by Orin Maddox</div>
    <div class="from">From Newyork</div>
  </div>
</aside>

<section class="abs partners" aria-label="Partner associations">
  <span class="badge" style="left:131px;width:74px"></span>
  <span class="badge" style="left:246px;width:52px"></span>
  <span class="badge" style="left:346px;width:164px"></span>
  <span class="badge" style="left:546px;width:110px"></span>
  <span class="badge" style="left:706px;width:176px"></span>
  <span class="badge" style="left:932px;width:146px"></span>
</section>

<footer class="abs footer">
  <div class="item" style="left:131px"><svg width="11" height="15" viewBox="0 0 13 18" style="margin-top:3px"><path d="M6.5 0C3 0 0 2.8 0 6.4 0 11 6.5 18 6.5 18S13 11 13 6.4C13 2.8 10 0 6.5 0z" fill="#ccc"/></svg><span>Address: 58 E. Tamsin Avenue, Ste<br>410, Pensacola, FL 32599</span></div>
  <div class="item email" style="left:405px"><svg width="13" height="10" viewBox="0 0 13 10" style="margin-top:5px"><rect width="13" height="10" fill="#ccc"/><path d="M0 0l6.5 5L13 0" fill="none" stroke="#3a3a3a"/></svg><span>Email: mirelharrowgate@quellmail.example</span></div>
  <div class="item" style="left:696px"><svg width="13" height="34" viewBox="0 0 13 34" style="margin-top:4px"><rect x="0" y="3" width="13" height="8" rx="2" fill="#ccc"/><rect x="2" y="22" width="9" height="12" rx="1" fill="#ccc"/></svg><span>Phone: (555) 261-0948<br>Mobile: (555) 718-3062</span></div>
  <div class="social" aria-label="Social media links"><b></b><b></b><b></b><b></b></div>
  <div class="rule"></div>
  <div class="copy">©2014 Harrowgate. All right reserved.</div>
</footer>

</body>
</html>
```